we can communicate on this, but i want to follow the approach we took on Pellew|Marsh & Quinlan but i feel the card front needs the black background and the platinum and gold logo. The back? I am open. we can use the same info from PM&Q. Velmont Arc is an enhanced equity investment fund - basically a very exclusive boutique hedge fund that uses only stock options. very advanced things. hope you are interested

Contact Information for Business Card

Dr. Lewis T. Brennick, CFA
Scientifique de fusée financière
701.555.0143
LTBquant47@mailvantor.com

4718 Willow Creek Bend W.
West Fargo, ND 58078

No web site

Colors

Designer to choose colors to be used in the design.

Requirements
Nice to have
• I tend to prefer the most visible applications of the logo to include logo and name, the logo version with a black background and the gold and platinum components separated by the black. I see this working well for a single side (logo and name - this is card front to me).
• I am fairly open to other treatments on the reverse side with the data. To me, it makes sense to have a different color rendition of the logo on the reverse and it may be a muted black tone on tone or an oversized portion that would have spot UV. Or, the reverse may play with colors and layout
Should not have
• Other colors = no no
• Decorative font

```html
<!DOCTYPE html>
<html lang="en">
<head>
<meta charset="utf-8">
<title>Velmont Arc – Business Card</title>
<link rel="stylesheet" href="https://fonts.googleapis.com/css2?family=Montserrat:wght@600;700&family=Open+Sans:wght@400;600&family=Roboto:wght@400&display=swap">
<style>
  :root {
    --backdrop: #d2d2d2;
    --paper: #ffffff;
    --ink: #161619;
    --gold: #d4af55;
    --text-grey: #444448;
    --card-w: 768px;
    --card-h: 437px;
  }
  * { box-sizing: border-box; margin: 0; padding: 0; }
  html, body {
    width: 1125px;
    height: 1200px;
    overflow: hidden;
    background: var(--backdrop);
  }
  .canvas {
    position: relative;
    width: 1125px;
    height: 1200px;
  }
  .card {
    position: absolute;
    left: 178px;
    width: var(--card-w);
    height: var(--card-h);
    border-radius: 24px;
    overflow: hidden;
    box-shadow: 0 3px 8px rgba(0,0,0,0.18);
  }
  .card--front { top: 140px; background: var(--paper); }
  .card--back  { top: 626px; background: var(--ink); }

  .card__art {
    position: absolute;
    inset: 0;
    width: 100%;
    height: 100%;
  }

  /* Front: brand block */
  .brand {
    position: absolute;
    left: 35px;
    top: 38px;
    width: 142px;
    display: flex;
    flex-direction: column;
    align-items: center;
  }
  .brand__dot {
    width: 66px;
    height: 66px;
    border-radius: 50%;
    background: var(--gold);
  }
  .brand__name {
    margin-top: 12px;
    font-family: "Montserrat", sans-serif;
    font-weight: 700;
    font-size: 19px;
    letter-spacing: 0.5px;
    color: var(--ink);
    white-space: nowrap;
  }

  /* Front: holder */
  .holder {
    position: absolute;
    right: 39px;
    top: 56px;
    text-align: right;
    font-family: "Open Sans", sans-serif;
  }
  .holder__name {
    font-weight: 600;
    font-size: 26px;
    line-height: 1.1;
    color: var(--gold);
    letter-spacing: 0.3px;
    white-space: nowrap;
  }
  .holder__role {
    margin-top: 6px;
    font-weight: 400;
    font-size: 20px;
    color: var(--ink);
    white-space: nowrap;
  }

  /* Front: contact */
  .address {
    position: absolute;
    left: 35px;
    top: 212px;
    font-family: "Roboto", sans-serif;
    font-style: normal;
    font-size: 17.5px;
    line-height: 22px;
    color: var(--text-grey);
  }
  .contact {
    position: absolute;
    left: 34px;
    top: 279px;
    list-style: none;
    font-family: "Roboto", sans-serif;
    font-size: 17.5px;
    color: var(--text-grey);
  }
  .contact__item {
    display: flex;
    align-items: center;
    height: 30px;
  }
  .contact__icon {
    width: 15px;
    height: 15px;
    margin-right: 11px;
    flex: none;
  }

  /* Back: brand */
  .brand-large {
    position: absolute;
    left: 0;
    right: 0;
    top: 100px;
    display: flex;
    flex-direction: column;
    align-items: center;
  }
  .brand-large__dot {
    width: 138px;
    height: 138px;
    border-radius: 50%;
    background: var(--gold);
  }
  .brand-large__name {
    margin-top: 28px;
    font-family: "Montserrat", sans-serif;
    font-weight: 700;
    font-size: 46px;
    letter-spacing: 1px;
    color: var(--paper);
    white-space: nowrap;
  }
</style>
</head>
<body>
<main class="canvas">

  <section class="card card--front" aria-label="Card front">
    <svg class="card__art" viewBox="0 0 768 437" aria-hidden="true">
      <path class="swoosh-black" fill="var(--ink)"
            d="M0,401 Q420,396 768,193 L768,204 Q470,385 40,437 L0,437 Z"/>
      <path class="swoosh-gold" fill="var(--gold)"
            d="M151,437 Q480,378 768,211 L768,437 Z"/>
      <circle class="seal" cx="446" cy="302" r="76" fill="var(--paper)" stroke="var(--ink)" stroke-width="5"/>
    </svg>

    <div class="brand">
      <div class="brand__dot"></div>
      <div class="brand__name">VELMONT ARC</div>
    </div>

    <div class="holder">
      <div class="holder__name">DR. LEWIS T. BRENNICK, CFA</div>
      <div class="holder__role">Scientifique de fusée financière</div>
    </div>

    <address class="address">
      4718 Willow Creek Bend W.<br>
      West Fargo, ND 58078
    </address>

    <ul class="contact">
      <li class="contact__item">
        <svg class="contact__icon" viewBox="0 0 16 16" aria-hidden="true">
          <path fill="var(--gold)" d="M3.2 1.2l2.4 0.4 1 3.2-1.6 1.2a8 8 0 0 0 4.8 4.8l1.2-1.6 3.2 1 0.4 2.4-1.8 1.8C6.4 14.4 1.6 9.6 1.4 3z"/>
        </svg>
        701.555.0143
      </li>
      <li class="contact__item">
        <svg class="contact__icon" viewBox="0 0 16 16" aria-hidden="true">
          <rect x="1" y="3" width="14" height="10" fill="var(--gold)"/>
          <path d="M3 5.5l5 4 5-4" fill="none" stroke="var(--paper)" stroke-width="1.6"/>
        </svg>
        LTBquant47@mailvantor.com
      </li>
    </ul>
  </section>

  <section class="card card--back" aria-label="Card back">
    <div class="brand-large">
      <div class="brand-large__dot"></div>
      <div class="brand-large__name">VELMONT ARC</div>
    </div>
  </section>

</main>
</body>
</html>
```